Locksmith Business Cards

My father-in-law is in need of new business cards for his locksmith business and I need to impress him. Kindly help me out!

You can see the previous business card attached. It is a family run business in North Wales.

No individual names on the cards.

Key Things to Feature:
- The words "Prompt", "Local", "Reliable" (as you can see under the logo on the website)
- 24h Emergency Service
- Covering All of North Wales, the Wirral and Chester
- The color blue
- A key or a lock would be interesting (similar to the ones that come up when you google locksmith business card)

Optional (only if design includes bullet points, like the example below):
https://imgvaultcdn.net/samples/208314/55172/55172_3904821_208314_image.jpg
- Residential / Commercial / Automotive
- Alarms & Cameras
- Key Cutting & Safes

https://www.brynhafod-locksmiths.co.uk/

Industry/Entity Type

Locksmith

Contact Information for Business Card

01632 960 418
07700 900 362
brynhafodlocksmiths@mailvane.com
Brynhafod Locksmiths, The Willow Barn, 7 Tannery Rd., Llandudno LL99 4QX
www.brynhafod-locksmiths.co.uk

Requirements
Must have
• - The words "Prompt", "Local", "Reliable" (as you can see under the logo on the website)
• - 24h Emergency Service
• - Covering All of North Wales, the Wirral and Chester
Nice to have
• - A key or a lock would be interesting (similar to the ones that come up when you google locksmith business card)

```html
<!DOCTYPE html>
<html lang="en">
<head>
<meta charset="utf-8">
<title>Brynhafod Locksmiths – Business Cards</title>
<link rel="stylesheet" href="https://fonts.googleapis.com/css2?family=Oswald:wght@500&family=Montserrat:wght@600&family=Roboto+Condensed:wght@400&display=swap">
<style>
  :root {
    --navy: #1f2a6e;
    --paper: #f2f2f0;
    --edge: #c8cbd4;
    --sky: #2f8fd8;
    --white: #ffffff;
    --emblem-light: #e6e9f3;
    --emblem-mid: #4a5aa6;
    --backdrop: #e4e5e8;
  }
  * { margin: 0; padding: 0; box-sizing: border-box; }
  html, body { width: 1200px; height: 1050px; overflow: hidden; }
  body {
    background: var(--backdrop);
    display: flex;
    flex-direction: column;
    align-items: center;
    justify-content: center;
    gap: 60px;
  }
  .card {
    position: relative;
    width: 700px;
    height: 400px;
    border-radius: 28px;
    overflow: hidden;
    background: var(--navy);
    box-shadow: 0 6px 18px rgba(0,0,0,.18);
  }
  .card__header {
    position: absolute;
    inset: 0 0 auto 0;
    height: 150px;
    background: var(--paper);
    border-bottom: 7px solid var(--edge);
    display: flex;
    align-items: center;
    padding-left: 44px;
    gap: 22px;
  }
  .brand__dot {
    width: 62px; height: 62px;
    border-radius: 50%;
    background: var(--navy);
    flex: none;
  }
  .brand__name {
    font-family: "Oswald", sans-serif;
    font-weight: 500;
    font-size: 50px;
    line-height: 1;
    color: var(--navy);
    letter-spacing: .5px;
    text-transform: uppercase;
  }
  .brand__tagline {
    margin-top: 8px;
    font-family: "Montserrat", sans-serif;
    font-weight: 600;
    font-size: 19px;
    letter-spacing: 5px;
    color: var(--navy);
    text-transform: uppercase;
  }
  .emblem {
    position: absolute;
    right: 40px;
    top: 178px;
    width: 150px;
    height: 150px;
    border-radius: 50%;
    background: radial-gradient(circle, var(--emblem-light) 0 45%, var(--emblem-mid) 46% 100%);
    border: 5px solid var(--white);
  }
  .card__body {
    position: absolute;
    left: 44px;
    top: 196px;
    max-width: 440px;
    color: var(--white);
    font-family: "Roboto Condensed", sans-serif;
    font-size: 20px;
    line-height: 1.5;
    list-style: none;
  }
  .services li {
    position: relative;
    padding-left: 26px;
  }
  .services li::before {
    content: "";
    position: absolute;
    left: 0; top: 12px;
    width: 8px; height: 8px;
    border-radius: 50%;
    background: var(--sky);
  }
  .contacts { top: 190px; }
  .contacts li {
    display: flex;
    align-items: flex-start;
    gap: 16px;
  }
  .contacts svg { width: 18px; height: 18px; flex: none; margin-top: 6px; fill: var(--sky); }
</style>
</head>
<body>

  <article class="card card--services">
    <header class="card__header">
      <span class="brand__dot"></span>
      <div class="brand">
        <div class="brand__name">Brynhafod Locksmiths</div>
        <div class="brand__tagline">Prompt | Local | Reliable</div>
      </div>
    </header>
    <ul class="card__body services">
      <li>Covering All of North Wales,<br>the Wirral and Chester</li>
      <li>Residential / Commercial / Automotive</li>
      <li>Alarms &amp; Cameras</li>
      <li>Key Cutting &amp; Safes</li>
    </ul>
    <div class="emblem" role="img" aria-label="24 hours emergency service emblem"></div>
  </article>

  <article class="card card--contact">
    <header class="card__header">
      <span class="brand__dot"></span>
      <div class="brand">
        <div class="brand__name">Brynhafod Locksmiths</div>
        <div class="brand__tagline">Prompt | Local | Reliable</div>
      </div>
    </header>
    <ul class="card__body contacts">
      <li><svg viewBox="0 0 24 24"><path d="M6.6 10.8a15 15 0 0 0 6.6 6.6l2.2-2.2a1 1 0 0 1 1-.25 11.4 11.4 0 0 0 3.6.57 1 1 0 0 1 1 1V20a1 1 0 0 1-1 1A17 17 0 0 1 3 4a1 1 0 0 1 1-1h3.5a1 1 0 0 1 1 1c0 1.25.2 2.45.57 3.57a1 1 0 0 1-.25 1z"/></svg>01632 960 418</li>
      <li><svg viewBox="0 0 24 24"><path d="M6.6 10.8a15 15 0 0 0 6.6 6.6l2.2-2.2a1 1 0 0 1 1-.25 11.4 11.4 0 0 0 3.6.57 1 1 0 0 1 1 1V20a1 1 0 0 1-1 1A17 17 0 0 1 3 4a1 1 0 0 1 1-1h3.5a1 1 0 0 1 1 1c0 1.25.2 2.45.57 3.57a1 1 0 0 1-.25 1z"/></svg>07700 900 362</li>
      <li><svg viewBox="0 0 24 24"><path d="M2 5h20v14H2z M3.5 6.5 12 13l8.5-6.5" fill="none" stroke="#2f8fd8" stroke-width="2"/></svg>brynhafodlocksmiths@mailvane.com</li>
      <li><svg viewBox="0 0 24 24"><circle cx="12" cy="12" r="9" fill="none" stroke="#2f8fd8" stroke-width="2"/><path d="M3 12h18M12 3c3 3 3 15 0 18M12 3c-3 3-3 15 0 18" fill="none" stroke="#2f8fd8" stroke-width="1.6"/></svg>www.brynhafod-locksmiths.co.uk</li>
      <li><svg viewBox="0 0 24 24"><path d="M12 2a7 7 0 0 0-7 7c0 5 7 13 7 13s7-8 7-13a7 7 0 0 0-7-7zm0 9.5A2.5 2.5 0 1 1 12 6.5a2.5 2.5 0 0 1 0 5z"/></svg><span>The Willow Barn, 7 Tannery Rd.,<br>Llandudno LL99 4QX</span></li>
    </ul>
    <div class="emblem" role="img" aria-label="24 hours emergency service emblem"></div>
  </article>

</body>
</html>
```